Briefpapier und Visitenkarten für Bayerisches Gasthaus mit Zimmer
Zielgruppe
Traditionelle Gaststätte im Zentrum einer Kleinstadt in Bayern. Direkt am Marktplatz. 10 Gästezimmer.
Bayerisch. Traditionell. Von junger Geschäftsführerin geführt, mit jungem Personal. Wir haben das Objekt erst vor Kurzem erworben und fangen gerade an.
Gerichte: Braten, Steaks, Brotzeiten, vegetarische und VEGANE Speisen
Getränke: Sehr bierlastig. Es war früher ein Brauereigasthaus. Heute gibts auch eine kleine feine Weinkarte.
Zielgruppe sind Einheimische und Touristen. Im Sommer kommen Radfahrer und Wanderer. Besonders angesprochen werden auch Kinder. Es gibt eine großzügige Spielecke.
Aufgabenstellung
Das Gasthaus heißt Falke. Daher spielt der Falke im Design auch eine wichtige Rolle.
Nachdem wir sehr familienorientiert sind, könnte ich mir auch eine Falke-Familie vorstellen.
Visitenkarten und Briefpapier sollen alle wichtigen Infos enthalten, aber dabei sehr klar gehalten werden und nicht überladen sein. Mir ist ein schlichtes und ansprechendes Design wichtig. Es soll nicht verspielt sein.
Hier ist die Homepage:
www.falke-haldenau-gast.de
Info auf Briefpapier:
GASTHAUS FALKE
Trauber GmbH
Als Info auf Visitenkarte:
Gasthaus Falke

```html
<!DOCTYPE html>
<html lang="de">
<head>
<meta charset="utf-8">
<title>Briefpapier – Gasthaus Falke</title>
<link rel="stylesheet" href="https://fonts.googleapis.com/css2?family=Roboto+Condensed:wght@300;400&display=swap">
<style>
  :root {
    --green: #a6c520;
    --text: #5a5a5a;
    --paper: #ffffff;
  }
  html, body { margin: 0; padding: 0; overflow: hidden; }
  body { width: 900px; height: 1200px; background: var(--paper); font-family: "Roboto Condensed", sans-serif; color: var(--text); }
  .letterhead { position: relative; width: 900px; height: 1200px; overflow: hidden; background: var(--paper); }
  .header-band { position: absolute; left: 107px; right: 0; top: 0; height: 122px; background: var(--green); }
  .header-rule { position: absolute; left: 107px; right: 0; top: 129px; height: 1px; background: var(--green); }
  .brand-name {
    position: absolute; left: 690px; top: 38px;
    color: var(--paper); font-weight: 400; font-size: 23px; line-height: 24px; letter-spacing: 2px;
  }
  .sender-line { position: absolute; left: 107px; top: 199px; font-size: 7.4px; letter-spacing: .4px; font-weight: 400; }
  .sender-line .dot { color: var(--green); }
  .contact { position: absolute; left: 678px; top: 198px; font-size: 10.5px; letter-spacing: .3px; }
  .contact .row { position: relative; padding-left: 14px; height: 17px; line-height: 17px; }
  .contact .row svg { position: absolute; left: 0; top: 3px; width: 10px; height: 11px; fill: var(--green); }
  .contact .company { color: var(--green); }
  .contact .gap { height: 4px; }
  .fold-mark { position: absolute; left: 0; width: 22px; height: 1px; background: var(--green); }
  .legal { position: absolute; left: 692px; top: 946px; font-size: 10.5px; letter-spacing: .3px; }
  .legal dt { color: var(--green); line-height: 17px; }
  .legal dd { margin: 0 0 4px 0; line-height: 17px; }
  .footer-band { position: absolute; left: 107px; right: 0; bottom: 0; height: 8px; background: var(--green); }
</style>
</head>
<body>
<div class="letterhead">
  <div class="header-band"></div>
  <div class="header-rule"></div>
  <div class="brand-name">GASTHAUS<br>FALKE</div>

  <div class="sender-line">GASTHAUS FALKE <span class="dot">•</span> Trauber GmbH <span class="dot">•</span> Marktplatz 5 <span class="dot">•</span> 84123 Haldenau</div>

  <div class="contact">
    <div class="row company">
      <svg viewBox="0 0 10 12"><path d="M5 0a4 4 0 0 0-4 4c0 3 4 8 4 8s4-5 4-8a4 4 0 0 0-4-4zm0 5.6a1.6 1.6 0 1 1 0-3.2 1.6 1.6 0 0 1 0 3.2z"/></svg>
      GASTHAUS FALKE
    </div>
    <div class="gap"></div>
    <div class="row">Trauber GmbH</div>
    <div class="row">Marktplatz 5</div>
    <div class="row">84123 Haldenau</div>
    <div class="gap"></div>
    <div class="row">
      <svg viewBox="0 0 10 10"><path d="M2 0l2 2-1 1.5c.8 1.6 2 2.8 3.5 3.5L8 6l2 2-1.5 2C4 10 0 6 0 1.5z"/></svg>
      09876 5432
    </div>
    <div class="gap"></div>
    <div class="row">
      <svg viewBox="0 0 10 10"><text x="0" y="9" font-size="11" font-family="Roboto Condensed, sans-serif" font-weight="400">@</text></svg>
      info@falke-haldenau-gast.de
    </div>
    <div class="row">
      <svg viewBox="0 0 10 10"><circle cx="5" cy="5" r="4.3" fill="none" stroke="#a6c520" stroke-width="1.2"/><path d="M.7 5h8.6M5 .7c-2 2.5-2 6 0 8.6M5 .7c2 2.5 2 6 0 8.6" fill="none" stroke="#a6c520" stroke-width=".9"/></svg>
      www.falke-haldenau-gast.de
    </div>
  </div>

  <div class="fold-mark" style="top:424px"></div>
  <div class="fold-mark" style="top:599px"></div>
  <div class="fold-mark" style="top:847px"></div>

  <dl class="legal">
    <dt>Steuernummer:</dt><dd>USt.-IdNr. DE xxx</dd>
    <dt>Handelsregister:</dt><dd>ORT</dd>
    <dt>Geschäftsführer:</dt><dd>Vorname Nachname</dd>
    <dt>Bank:</dt><dd>Musterbank</dd>
    <dd>IBAN DExx xxxx xxxx xxxx xxxx xx<br>BIC XXXXXXX 1XXX</dd>
    <dt>Kontoinhaber:</dt><dd>Trauber GmbH</dd>
  </dl>

  <div class="footer-band"></div>
</div>
</body>
</html>
```